NEW Modern Sleek Business Card for VR Language Startup

Our startup is using VR to lead the next wave of world language education. We need a two-sided business card that introduces the larger organization (Brightloom Language Inc) and our contact info on one side and shows the product, Glimwoorld, on the other side.

Side 1 (contact info)= Brightloom Logo and Contact info (name, title, phone, email)

Side 2 (product)= Glimworld logo, text, and website
Text= Culturally Immersive Language Learning Games
Website= www.glimworld-play.com

Target Market(s)

Education, Technology

Contact Information for Business Card

Contact info will be updated upon approval of the design. For now, put this as a placeholder.

Perry Dunmore
Founder & CEO
pdunmore@quillpost-mail.net
(555)-014-2286

Font styles to use
Other font styles liked:
• Gibson and Century Gothic are the brand fonts

Requirements
Nice to have
• I would love to see cohesion between the design and colors of the two logos. I have attached a few business card designs that I like, so you can get a feel for my preferred style.

```html
<!DOCTYPE html>
<html lang="en">
<head>
<meta charset="utf-8">
<title>Brightloom Language — Business Card</title>
<link href="https://fonts.googleapis.com/css2?family=Montserrat:wght@300;400;600;700&family=Roboto:wght@400;500;700&display=swap" rel="stylesheet">
<style>
  :root {
    --page-bg: #e4e5e7;
    --card-white: #ffffff;
    --card-black: #1e1e1e;
    --ink: #2a2a2a;
    --ink-soft: #555a60;
    --name-blue: #3a8ff0;
    --title-orange: #ff7a2e;
    --link-blue: #4f6cf2;
    --line-blue: #5a78f0;
    --on-dark: #ffffff;
  }
  * { box-sizing: border-box; margin: 0; padding: 0; }
  html, body { width: 1200px; height: 800px; overflow: hidden; }
  body {
    background: var(--page-bg);
    display: flex;
    align-items: center;
    justify-content: center;
    gap: 44px;
    font-family: "Roboto", Arial, sans-serif;
  }
  .card {
    width: 540px;
    height: 309px;
    position: relative;
    overflow: hidden;
    box-shadow: 0 10px 28px rgba(0,0,0,0.14);
  }

  /* Product side */
  .card--product {
    background: var(--card-white);
    display: flex;
    flex-direction: column;
    align-items: center;
    justify-content: center;
  }
  .lockup {
    display: flex;
    align-items: center;
    gap: 16px;
  }
  .product-name {
    font-family: "Montserrat", Arial, sans-serif;
    font-weight: 400;
    font-size: 40px;
    color: var(--ink-soft);
    letter-spacing: -0.5px;
  }
  .lockup-divider {
    width: 1px;
    height: 44px;
    background: var(--line-blue);
    opacity: 0.6;
  }
  .company-mark { display: flex; flex-direction: column; line-height: 1; }
  .company-name {
    font-family: "Montserrat", Arial, sans-serif;
    font-weight: 700;
    font-size: 24px;
    letter-spacing: 3px;
    color: var(--ink);
  }
  .company-sub {
    font-family: "Montserrat", Arial, sans-serif;
    font-weight: 300;
    font-size: 11px;
    letter-spacing: 8.6px;
    color: var(--ink);
    margin-top: 5px;
  }
  .tagline {
    margin-top: 22px;
    font-size: 14px;
    font-weight: 500;
    color: var(--ink);
  }
  .web-row {
    margin-top: 10px;
    display: flex;
    align-items: center;
    gap: 10px;
    width: 440px;
  }
  .web-line { flex: 1; height: 26px; }
  .website { font-size: 14px; color: var(--link-blue); white-space: nowrap; }

  /* Contact side */
  .card--contact { background: var(--card-black); }
  .contact-panel {
    position: absolute;
    inset: 0;
    width: 100%;
    height: 100%;
  }
  .contact-brand {
    position: absolute;
    left: 36px;
    top: 36px;
    line-height: 1;
  }
  .contact-brand .company-name { color: var(--on-dark); font-size: 28px; }
  .contact-brand .company-sub { color: var(--on-dark); font-size: 12px; letter-spacing: 10.5px; }
  .contact-details {
    position: absolute;
    left: 36px;
    top: 142px;
  }
  .person-name {
    font-size: 22px;
    font-weight: 700;
    color: var(--name-blue);
  }
  .person-title {
    font-size: 14px;
    font-weight: 500;
    color: var(--title-orange);
    margin-top: 2px;
  }
  .contact-list { list-style: none; margin-top: 14px; }
  .contact-list li {
    display: flex;
    align-items: center;
    gap: 8px;
    color: var(--on-dark);
    font-size: 13px;
    margin-bottom: 6px;
  }
  .contact-list svg { width: 12px; height: 12px; flex: none; }
</style>
</head>
<body>

  <section class="card card--product" aria-label="Product side">
    <div class="lockup">
      <span class="product-name">Glimworld</span>
      <span class="lockup-divider"></span>
      <div class="company-mark">
        <span class="company-name">BRIGHTLOOM</span>
        <span class="company-sub">LANGUAGE</span>
      </div>
    </div>
    <p class="tagline">Culturally Immersive Language Learning Games</p>
    <div class="web-row">
      <svg class="web-line" viewBox="0 0 100 26" preserveAspectRatio="none" aria-hidden="true">
        <line x1="0" y1="13" x2="94" y2="13" stroke="#5a78f0" stroke-width="1.2" vector-effect="non-scaling-stroke"/>
      </svg>
      <span class="website">www.glimworld-play.com</span>
      <svg class="web-line" viewBox="0 0 100 26" preserveAspectRatio="none" aria-hidden="true">
        <line x1="6" y1="13" x2="100" y2="13" stroke="#5a78f0" stroke-width="1.2" vector-effect="non-scaling-stroke"/>
      </svg>
    </div>
  </section>

  <section class="card card--contact" aria-label="Contact side">
    <svg class="contact-panel" viewBox="0 0 540 309" aria-hidden="true">
      <path d="M540 60 C470 60 420 90 400 150 C380 210 400 270 440 309 L540 309 Z" fill="#ffffff"/>
    </svg>
    <div class="contact-brand">
      <span class="company-name">BRIGHTLOOM</span><br>
      <span class="company-sub">LANGUAGE</span>
    </div>
    <div class="contact-details">
      <p class="person-name">Perry Dunmore</p>
      <p class="person-title">Founder &amp; CEO</p>
      <ul class="contact-list">
        <li>
          <svg viewBox="0 0 24 24" aria-hidden="true"><path fill="#3a8ff0" d="M6.6 10.8a15 15 0 0 0 6.6 6.6l2.2-2.2c.3-.3.7-.4 1-.2 1.1.4 2.3.6 3.6.6.6 0 1 .4 1 1V20c0 .6-.4 1-1 1A17 17 0 0 1 3 4c0-.6.4-1 1-1h3.5c.6 0 1 .4 1 1 0 1.3.2 2.5.6 3.6.1.3 0 .7-.2 1z"/></svg>
          (555)-014-2286
        </li>
        <li>
          <svg viewBox="0 0 24 24" aria-hidden="true"><rect x="2" y="5" width="20" height="14" rx="2" fill="#3a8ff0"/><path d="M3 6l9 7 9-7" fill="none" stroke="#1e1e1e" stroke-width="1.8"/></svg>
          pdunmore@quillpost-mail.net
        </li>
      </ul>
    </div>
  </section>

</body>
</html>
```